Website for legal expungement services with button to qualify/disqualify potential clients

Brightpath Record Renewal, LLC is a law firm focusing in legal expungement servcies (allowing people to erase criminal court records, police records, proseution files, etc). I want a more modern look which exudes confidence in the services. I am looking for a clean website that looks very polished. I want to keep the pages to a minimum, as I want the page not so much to answer questions, but to direct traffic to contact the law office. I would like the main focus point to be an button which would take a client through a series of questions to see if they would qualify for the services; this serves two purposes 1) to collect contact info for future marketing via email and 2) eliminate individuals who we are currently unable to help. A current theme that I have played around with are "Change so much, you'll need to reintroduce yourself" alongside a picture of a guys hand outstretched.
On the landing page, I would like a very brief and to the point explanation of what the service would be (i.e. "Leave your past in the past; expunge all your criminal records" ), followed by a list of benefits that it provides. (NB: included is a file "law post card-02" that includes the main benefits to expungement). Also included are two logo files for a more updated logo I currently use ("BRR Logo" and BRR Logo2") (NB: I'm open to revisions on this as well). Lastly, I've had two very minor 'ads' that I did ("postcard back" and "KVT Ad") that I like the idea of.

Target Market(s)

Middle/upper-middle class, mostly male, people with a criminal record or criminal accusation

Industry/Entity Type

Legal Services

Coding

Coded - Design and coding required

Requirements
Must have
• Button that attracts attention up front (possibly stand out coloring) to click to open up a series of questions to qualify/eliminate prospects, and simultaneously gather their info. Also, must be mobile friendly.

```html
<!DOCTYPE html>
<html lang="en">
<head>
<meta charset="utf-8">
<title>Brightpath Record Renewal</title>
<link rel="stylesheet" href="https://fonts.googleapis.com/css2?family=Poppins:wght@400;500;600;700&display=swap">
<style>
:root{
  --navy:#0d3a73;
  --blue:#1f88d0;
  --blue-deep:#1679c6;
  --yellow:#fcb414;
  --ink:#111418;
  --grey:#6a6a6a;
  --tick:#2bb24c;
  --white:#ffffff;
  --footer:#0b0b0b;
}
*{box-sizing:border-box;margin:0;padding:0}
html,body{width:1200px;height:3772px;overflow:hidden}
body{position:relative;font-family:'Poppins',sans-serif;background:var(--white);color:var(--ink)}
.abs{position:absolute}
.brand{display:flex;align-items:center;gap:12px;color:var(--navy);font-weight:600;white-space:nowrap}
.brand-mark{width:18px;height:18px;background:var(--navy);flex:none}

/* header */
.site-header{left:0;top:0;width:1200px;height:85px;background:var(--white)}
.site-header .brand{position:absolute;left:110px;top:30px;font-size:18px}
.main-nav{position:absolute;left:412px;top:33px;display:flex;gap:22px;font-size:14px;font-weight:500}
.phone-pill{position:absolute;left:946px;top:22px;width:144px;height:42px;border-radius:21px;background:var(--navy);color:var(--white);display:flex;align-items:center;justify-content:center;gap:8px;font-size:14px;font-weight:600}

/* hero */
.hero{left:0;top:85px;width:1200px;height:601px;background:linear-gradient(100deg,#2b3a4e 0%,#1b2430 40%,#0e1218 70%,#08090c 100%)}
.hero h1{position:absolute;left:0;width:1200px;top:163px;text-align:center;color:var(--white);font-size:55px;line-height:52px;font-weight:700;letter-spacing:-0.5px}
.btn{display:inline-flex;align-items:center;justify-content:center;border-radius:21px;font-size:13px;font-weight:600;color:var(--white)}
.btn-yellow{background:var(--yellow)}
.btn-navy{background:var(--navy)}
.hero .btn{position:absolute;left:502px;top:321px;width:197px;height:40px}
.scroll-down{left:566px;top:649px;width:64px;height:64px;border-radius:50%;background:var(--white);box-shadow:0 2px 8px rgba(0,0,0,.25);display:flex;align-items:center;justify-content:center}

/* services */
.section-title{position:absolute;left:0;width:1200px;text-align:center;font-size:36px;font-weight:600}
.service-card{width:407px;height:528px;top:875px;background:var(--white);box-shadow:0 2px 10px rgba(0,0,0,.16);text-align:center}
.service-card .photo{position:absolute;left:9px;top:10px;width:389px;height:228px}
.service-card h3{position:absolute;left:20px;right:20px;top:258px;font-size:21px;line-height:29px;font-weight:600}
.service-card p{position:absolute;left:40px;right:40px;top:334px;font-size:13.5px;line-height:29px;color:var(--grey)}
.service-card .btn{position:absolute;left:153px;top:462px;width:110px;height:42px}

/* about */
.about{left:0;top:1488px;width:1200px;height:415px;background:linear-gradient(90deg,var(--blue) 0%,#2a8fd4 50%,var(--blue) 100%);color:var(--white);text-align:center}
.about h2{position:absolute;left:0;width:1200px;top:38px;font-size:36px;font-weight:700}
.about p{position:absolute;left:158px;width:884px;top:100px;font-size:13.5px;line-height:29px}
.about .btn{position:absolute;left:538px;top:321px;width:109px;height:42px}

/* benefits */
.benefits-intro{left:160px;width:880px;top:2025px;text-align:center;font-size:13.5px;line-height:29px;color:var(--grey)}
.benefit{width:210px;text-align:center;color:var(--grey);font-size:16px;line-height:29px}
.benefit .icon{width:90px;height:90px;border-radius:50%;background:var(--blue-deep);margin:0 auto 14px;display:flex;align-items:center;justify-content:center}
.benefit.active{background:var(--white);box-shadow:0 2px 10px rgba(0,0,0,.18);padding-top:15px;height:229px}

/* records */
.records{left:0;top:2717px;width:1200px;height:406px;background:linear-gradient(90deg,#1a78c4 0%,var(--blue) 100%);color:var(--white)}
.records .photo{position:absolute;left:138px;top:74px;width:419px;height:263px;background:linear-gradient(120deg,#5b6c7c,#8a9aa6 50%,#3f4b57)}
.records h2{position:absolute;left:598px;top:68px;font-size:34px;line-height:52px;font-weight:700}
.tick-list{list-style:none}
.tick-list li{display:flex;align-items:center;gap:10px;height:31px;font-size:16px;font-weight:500}
.tick{width:20px;height:20px;flex:none}
.records .tick-list{position:absolute;left:604px;top:182px}

/* cases */
.cases h2{left:110px;top:3165px;font-size:34px;line-height:52px;font-weight:700}
.cases .tick-list{position:absolute;left:110px;top:3286px}
.cases .tick-list li{font-weight:400;color:var(--ink)}
.cases .btn{left:107px;top:3404px;width:195px;height:42px}
.cases-brand{left:640px;top:3270px;font-size:30px}
.cases-brand .brand-mark{width:30px;height:30px}

/* footer */
.site-footer{left:0;top:3500px;width:1200px;height:272px;background:var(--footer);color:var(--white);text-align:center}
.site-footer .brand{position:absolute;left:0;width:1200px;top:76px;justify-content:center;color:var(--white);font-size:20px}
.site-footer .brand-mark{background:var(--white)}
.footer-phone{position:absolute;left:0;width:1200px;top:156px;display:flex;justify-content:center;align-items:center;gap:12px;font-size:14px;font-weight:600}
.footer-nav{position:absolute;left:0;width:1200px;top:204px;display:flex;justify-content:center;gap:24px;font-size:14px;font-weight:500}
.footer-rule{position:absolute;left:110px;width:980px;top:234px;height:1px;background:#3a3a3a}
.copyright{position:absolute;left:0;width:1200px;top:243px;font-size:12.5px}
</style>
</head>
<body>

<header class="abs site-header">
  <div class="brand"><span class="brand-mark"></span>Brightpath Record Renewal</div>
  <nav class="main-nav"><span>Home</span><span>About Us</span><span>Services</span><span>Benifits To Expungement</span><span>Contact Us</span></nav>
  <div class="phone-pill">
    <svg width="16" height="16" viewBox="0 0 24 24"><path fill="#fff" d="M6.6 10.8a15.1 15.1 0 0 0 6.6 6.6l2.2-2.2a1 1 0 0 1 1-.25 11.4 11.4 0 0 0 3.6.57 1 1 0 0 1 1 1V20a1 1 0 0 1-1 1A17 17 0 0 1 3 4a1 1 0 0 1 1-1h3.5a1 1 0 0 1 1 1c0 1.25.2 2.45.57 3.57a1 1 0 0 1-.25 1z"/></svg>
    505-555-0148
  </div>
</header>

<section class="abs hero" role="img" aria-label="Man in a dark suit holding out an open hand">
  <h1>"Change so much, you'll need<br>to reintroduce yourself"</h1>
  <span class="btn btn-yellow">Book An Appointment</span>
</section>
<div class="abs scroll-down">
  <svg width="30" height="18" viewBox="0 0 30 18"><path d="M3 3l12 12L27 3" fill="none" stroke="#111" stroke-width="3.5" stroke-linecap="round" stroke-linejoin="round"/></svg>
</div>

<h2 class="section-title" style="top:753px">Our Services</h2>

<article class="abs service-card" style="left:110px">
  <div class="photo" role="img" aria-label="Hands holding a tablet showing criminal records" style="background:linear-gradient(135deg,#1e4f86,#4d8fcf 45%,#cfe3f3 70%,#6fa7d8)"></div>
  <h3>Collect Contact Info For Future Marketing Via Email</h3>
  <p>Lorem Ipsum is simply dummy text of the printing and typesetting industry. Lorem Ipsum has been the industry's standard dummy text ever since the 1500s</p>
  <span class="btn btn-navy">Read More</span>
</article>
<article class="abs service-card" style="left:675px">
  <div class="photo" role="img" aria-label="Two people reviewing a document beside a laptop" style="background:linear-gradient(135deg,#2c3036,#8a8f96 45%,#e4e6e8 70%,#a9adb2)"></div>
  <h3>Eliminate Individuals Who We Are Currently Unable To Help</h3>
  <p>Lorem Ipsum is simply dummy text of the printing and typesetting industry. Lorem Ipsum has been the industry's standard dummy text ever since the 1500s</p>
  <span class="btn btn-navy">Read More</span>
</article>

<section class="abs about">
  <h2>About Us</h2>
  <p>Lorem Ipsum is simply dummy text of the printing and typesetting industry. Lorem Ipsum has been the industry's standard dummy text ever since the 1500s Lorem Ipsum is simply dummy text of the printing and typesetting industry. Lorem Ipsum has been the industry's standard dummy text ever since the 1500s Lorem Ipsum is simply dummy text of the printing and typesetting industry. Lorem Ipsum has been the industry's standard dummy text ever since the 1500s Lorem Ipsum is simply dummy text of the printing and typesetting industry. Lorem Ipsum has been the industry's standard dummy text ever since the 1500s Lorem Ipsum is simply dummy text of the printing and typesetting industry. Lorem Ipsum has been the industry's standard dummy text ever since the 1500s</p>
  <span class="btn btn-navy">Read More</span>
</section>

<h2 class="section-title" style="top:1950px">Benifits Of Expunging</h2>
<p class="abs benefits-intro">Brightpath Record Renewal is 5-star rated firm. which has been formed with the passing of the new state expungement law of 2020. it is a subdivision of the Harlow law firm, and since its creation has helped over 100 local citizens successfully expunge their criminal records.</p>

<div class="abs benefit" style="left:103px;top:2164px">
  <div class="icon"><svg width="44" height="44" viewBox="0 0 44 44"><circle cx="24" cy="15" r="10" fill="none" stroke="#fff" stroke-width="3"/><text x="24" y="20" fill="#fff" font-size="14" font-weight="700" text-anchor="middle" font-family="Poppins,sans-serif">$</text><path d="M4 34h10l8 4 14-6" fill="none" stroke="#fff" stroke-width="3" stroke-linecap="round"/></svg></div>
  Make and better job opportunities Leading to higher income
</div>
<div class="abs benefit active" style="left:366px;top:2150px">
  <div class="icon"><svg width="44" height="44" viewBox="0 0 44 44"><rect x="10" y="8" width="24" height="14" rx="3" fill="none" stroke="#fff" stroke-width="3" transform="rotate(-20 22 15)"/><path d="M4 34h10l8 4 14-6" fill="none" stroke="#fff" stroke-width="3" stroke-linecap="round"/></svg></div>
  Loan qualification and better loan rates
</div>
<div class="abs benefit" style="left:625px;top:2164px">
  <div class="icon"><svg width="44" height="44" viewBox="0 0 44 44"><path d="M22 5l14 5v10c0 9-6 15-14 19C14 35 8 29 8 20V10z" fill="#fff"/><rect x="18" y="20" width="8" height="8" fill="#1679c6"/><circle cx="22" cy="18" r="3" fill="none" stroke="#1679c6" stroke-width="2"/></svg></div>
  Protecting Your Privacy
</div>
<div class="abs benefit" style="left:888px;top:2164px">
  <div class="icon"><svg width="48" height="44" viewBox="0 0 48 44"><path d="M24 8L4 17l20 9 20-9z" fill="#fff"/><path d="M12 22v9c4 4 20 4 24 0v-9l-12 5z" fill="#fff"/></svg></div>
  Better Education Opportunities
</div>

<div class="abs benefit" style="left:103px;top:2441px">
  <div class="icon"><svg width="44" height="44" viewBox="0 0 44 44"><rect x="9" y="7" width="26" height="30" rx="3" fill="none" stroke="#fff" stroke-width="3"/><circle cx="22" cy="24" r="6" fill="none" stroke="#fff" stroke-width="2.5"/><path d="M15 13h14" stroke="#fff" stroke-width="3"/></svg></div>
  Removing the stigma of having a criminal record
</div>
<div class="abs benefit" style="left:366px;top:2441px">
  <div class="icon"><svg width="46" height="44" viewBox="0 0 46 44"><path d="M23 6L3 24h6v14h10v-9h8v9h10V24h6z" fill="#fff"/></svg></div>
  More Option For Housing
</div>
<div class="abs benefit" style="left:625px;top:2441px">
  <div class="icon"><svg width="44" height="44" viewBox="0 0 44 44"><path d="M12 6h20v10c0 6-4 10-10 10S12 22 12 16z" fill="#fff"/><path d="M12 9H6c0 6 3 9 7 9M32 9h6c0 6-3 9-7 9" fill="none" stroke="#fff" stroke-width="2.5"/><rect x="19" y="26" width="6" height="6" fill="#fff"/><rect x="13" y="32" width="18" height="5" fill="#fff"/></svg></div>
  Qualifying for government assistance programs
</div>
<div class="abs benefit" style="left:888px;top:2441px">
  <div class="icon"><svg width="46" height="44" viewBox="0 0 46 44"><rect x="5" y="16" width="28" height="18" rx="3" fill="#fff"/><rect x="5" y="21" width="28" height="3" fill="#1679c6"/><path d="M32 6l9 3v7c0 6-4 9-9 12-5-3-9-6-9-12V9z" fill="#fff" stroke="#1679c6" stroke-width="2"/></svg></div>
  Lower Insurance premiums
</div>

<section class="abs records">
  <div class="photo" role="img" aria-label="Smiling man in a suit talking across a desk"></div>
  <h2>How Your Records Are<br>Seen By the Public :</h2>
  <ul class="tick-list">
    <li><svg class="tick" viewBox="0 0 20 20"><circle cx="10" cy="10" r="10" fill="#2bb24c"/><path d="M5.5 10.5l3 3 6-6.5" fill="none" stroke="#fff" stroke-width="2.4" stroke-linecap="round" stroke-linejoin="round"/></svg>Public reporting (www.statecourtrecords.gov)</li>
    <li><svg class="tick" viewBox="0 0 20 20"><circle cx="10" cy="10" r="10" fill="#2bb24c"/><path d="M5.5 10.5l3 3 6-6.5" fill="none" stroke="#fff" stroke-width="2.4" stroke-linecap="round" stroke-linejoin="round"/></svg>Police Reports</li>
    <li><svg class="tick" viewBox="0 0 20 20"><circle cx="10" cy="10" r="10" fill="#2bb24c"/><path d="M5.5 10.5l3 3 6-6.5" fill="none" stroke="#fff" stroke-width="2.4" stroke-linecap="round" stroke-linejoin="round"/></svg>State Department Of Public Safety</li>
    <li><svg class="tick" viewBox="0 0 20 20"><circle cx="10" cy="10" r="10" fill="#2bb24c"/><path d="M5.5 10.5l3 3 6-6.5" fill="none" stroke="#fff" stroke-width="2.4" stroke-linecap="round" stroke-linejoin="round"/></svg>District Attorney Prosecution Files</li>
    <li><svg class="tick" viewBox="0 0 20 20"><circle cx="10" cy="10" r="10" fill="#2bb24c"/><path d="M5.5 10.5l3 3 6-6.5" fill="none" stroke="#fff" stroke-width="2.4" stroke-linecap="round" stroke-linejoin="round"/></svg>Court Records</li>
  </ul>
</section>

<section class="cases">
  <h2 class="abs">What Types Of Cases<br>Qualify</h2>
  <ul class="tick-list">
    <li><svg class="tick" viewBox="0 0 20 20"><circle cx="10" cy="10" r="10" fill="#2bb24c"/><path d="M5.5 10.5l3 3 6-6.5" fill="none" stroke="#fff" stroke-width="2.4" stroke-linecap="round" stroke-linejoin="round"/></svg>Criminal Accusations that were dismissed</li>
    <li><svg class="tick" viewBox="0 0 20 20"><circle cx="10" cy="10" r="10" fill="#2bb24c"/><path d="M5.5 10.5l3 3 6-6.5" fill="none" stroke="#fff" stroke-width="2.4" stroke-linecap="round" stroke-linejoin="round"/></svg>Criminal Cases that went into a Diversionary Program</li>
    <li><svg class="tick" viewBox="0 0 20 20"><circle cx="10" cy="10" r="10" fill="#2bb24c"/><path d="M5.5 10.5l3 3 6-6.5" fill="none" stroke="#fff" stroke-width="2.4" stroke-linecap="round" stroke-linejoin="round"/></svg>Convictions</li>
  </ul>
  <span class="abs btn btn-yellow">Book An Appointment</span>
  <div class="abs brand cases-brand"><span class="brand-mark"></span>Brightpath Record Renewal</div>
</section>

<footer class="abs site-footer">
  <div class="brand"><span class="brand-mark"></span>Brightpath Record Renewal</div>
  <div class="footer-phone">
    <svg width="26" height="26" viewBox="0 0 26 26"><rect width="26" height="26" rx="5" fill="#fff"/><path fill="#0b0b0b" d="M8.8 11.9a10 10 0 0 0 4.4 4.4l1.5-1.5a.7.7 0 0 1 .7-.17 7.6 7.6 0 0 0 2.4.38.7.7 0 0 1 .7.7v2.3a.7.7 0 0 1-.7.7A11.4 11.4 0 0 1 6.4 7.3a.7.7 0 0 1 .7-.7h2.3a.7.7 0 0 1 .7.7c0 .84.13 1.64.38 2.4a.7.7 0 0 1-.17.7z"/></svg>
    505-555-0148
  </div>
  <nav class="footer-nav"><span>Home</span><span>About Us</span><span>Services</span><span>Benifits To Expungement</span><span>Contact Us</span></nav>
  <div class="footer-rule"></div>
  <p class="copyright">© 2023.Brightpath Record Renewal | All Rights Reserved.</p>
</footer>

</body>
</html>
```